New Business Card for our Indoor Golf Training Facility

We are looking for designs for a new business card for our indoor golf training facility. Attached is our logo, our logo with our slogan, and here is our elevator pitch (What makes us different from the others) not sure if all the info will fit on one card, maybe you can condense the elevator pitch? here is the info

Elevator Pitch
We work with serious golfers and those that want to be serious golfers…
to make you better, faster, at all phases of the game…
We use the same state-of-the-art technology as professional golfers…
which produces data sets that shows your improvement in real time.
Our facility is available 24/7 to our members, which allows you to improve on your time.

our website: www.birchpinlinks.com

Target Market(s)

Golfers

Font styles to use
Serif
Sans Serif

Colors
ec1f27
f59195
fbd4d5
919191
d3d3d3
1b1b1b

Requirements
Must have
• our logo or our logo with the slogan, elevator pitch (can be condensed or shortened)

```html
<!DOCTYPE html>
<html lang="en">
<head>
<meta charset="utf-8">
<title>Birch Pin Links – Business Card</title>
<link href="https://fonts.googleapis.com/css2?family=Open+Sans:wght@400;600;700&family=Source+Sans+3:ital,wght@0,400;0,700;1,700&display=swap" rel="stylesheet">
<style>
  :root {
    --brand-red: #ec1f27;
    --card-red: #e83c33;
    --paper: #eeeeee;
    --ink: #1b1b1b;
    --rule-grey: #919191;
    --backdrop: #2b2b2b;
    --white: #ffffff;
  }
  * { margin: 0; padding: 0; box-sizing: border-box; }
  html, body { width: 1200px; height: 1200px; overflow: hidden; }
  body { background: var(--backdrop); position: relative; }

  .card {
    position: absolute;
    top: 310px;
    width: 366px;
    height: 594px;
    text-align: center;
  }
  .card--front { left: 233px; background: var(--paper); font-family: "Open Sans", sans-serif; color: var(--ink); }
  .card--back { left: 628px; width: 368px; background: var(--card-red); font-family: "Source Sans 3", sans-serif; color: var(--white); }

  .brand { position: absolute; top: 156px; left: 0; width: 100%; text-align: center; }
  .brand__name { font-weight: 700; font-size: 36px; line-height: 1; color: var(--brand-red); letter-spacing: -0.3px; }
  .brand__slogan { font-size: 12.5px; color: var(--brand-red); margin-top: 7px; }

  .contact { position: absolute; top: 364px; left: 0; width: 100%; }
  .contact__name { font-size: 26px; color: var(--brand-red); line-height: 1.2; }
  .contact__title { font-size: 17px; line-height: 1.3; }
  .contact__rule { width: 164px; height: 1px; background: var(--rule-grey); margin: 10px auto 10px; }
  .contact__line { font-size: 17px; line-height: 1.3; }

  .pitch__heading { position: absolute; top: 131px; width: 100%; font-weight: 700; font-size: 22px; letter-spacing: 0.5px; }
  .pitch__body { position: absolute; top: 187px; width: 100%; font-size: 19.5px; line-height: 24px; }
  .pitch__body p + p { margin-top: 20px; }
  .pitch__rule { position: absolute; top: 515px; left: 32px; width: 304px; height: 1px; background: rgba(255,255,255,0.8); }
  .pitch__cta { position: absolute; top: 526px; width: 100%; font-size: 16.5px; }
  .pitch__cta em { font-weight: 700; }
</style>
</head>
<body>
  <section class="card card--front">
    <div class="brand">
      <div class="brand__name">Birch Pin Links</div>
      <div class="brand__slogan">Train Smarter. Score Lower. Play More.</div>
    </div>
    <div class="contact">
      <div class="contact__name">Daniel Hargrove</div>
      <div class="contact__title">Managing Director</div>
      <div class="contact__rule"></div>
      <div class="contact__line">555-014-2230</div>
      <div class="contact__line">www.birchpinlinks.com</div>
      <div class="contact__rule"></div>
      <div class="contact__line">1480 Ridgeline Ave. Suite B4</div>
      <div class="contact__line">Maple Fork, OH 45099</div>
    </div>
  </section>

  <section class="card card--back">
    <h2 class="pitch__heading">ELEVATOR PITCH</h2>
    <div class="pitch__body">
      <p>We work with serious golfers and<br>those that want to be serious golfers…<br>to make you better, faster<br>at all phases of the game…</p>
      <p>We use the same state-of-the-art<br>technology as professional golfers…<br>which produces data sets that shows<br>your improvement in real time.</p>
      <p>Our facility is available 24/7 to<br>our members which allows you<br>to improve on your time.</p>
    </div>
    <div class="pitch__rule"></div>
    <p class="pitch__cta">Visit <em>www.birchpinlinks.com</em> for more details.</p>
  </section>
</body>
</html>
```